Migration and redesign of existing website to WordPress using DIVI 3

I. TASK OBJECTIVE:
- Redesign our existing website www.kelvaleheelcare.com.au with a fresh new look and migrate to new Wordpress site based on DIVI3 theme. The site will contain the same basic functionality as the existing site (with some small changes).

II. STYLE/ DESIGN ASPECT:
As an example of a site that I like the look of, see https://pebblequarn.com/. I like the use of shadows, and this would go well with the little animations you can do with Divi (e.g. when hovering over pics).

1. What I am looking for is a design which has lots of white space, is modern and friendly looking (but still not too cute or frivolous, as we are a medical practice)
2. DESIGN that is NOT TOO rectangular or blocky.
3. Please take into consideration our Users are Older market, so any icons or navigation features need to be very easy to understand and not too small.
4. Must be easy to navigate
5. We are are happy to go with a new colour scheme, and are working on some ideas for this, but happy to take suggestions.

III. SPECIFICATIONS:
1. 5+ Pages (should flow like the current site)
2. Using Wordpress Divi 3 theme.
3. I'd like every page to have a "book now" button and a contact form in a sidebar so that users can click the button or fill in the contact form without scrolling at all. EXCEPT ON THE HOME PAGE, where there should still be a book now button (maybe on the top right in the header of all pages?), and maybe a contact us button which scrolls down to the contact area at the bottom of the HOME page. I don't think a side bar is necessarily required on the home page, but if you think it makes sense from a design perspective please let me know.
4. AT THE BOTTOM OF THE PAGE, just above the FOOTER, I'd like a row of trust logos for various organisations that we are affiliated with. (A list of this company will be provided later but you could temporarily use placeholders)

Once we have a structure in place, we can migrate most of the content. Please let me know if I'm not being clear or you need further information.

Podiatry Customers and Referrors

Health Care

5+ page

• Simple to navigate.
• Contact/booking details on most if not all pages - please see specification above
• Section for Trusted Affiliates above the footer
• Wordpress using Divi3 Theme
• Not too busy with the design. Plenty of white space or light background.
• Should not be complicated to navigate.
• TOO rectangular or blocky designs

```html
<!DOCTYPE html>
<html lang="en">
<head>
<meta charset="utf-8">
<title>Kelvale Heel Care – Podiatry</title>
<link href="https://fonts.googleapis.com/css2?family=Alegreya+Sans:wght@700;800&family=Lato:wght@300;400;700;900&display=swap" rel="stylesheet">
<style>
:root{
  --blue:#7fb9d1;
  --blue-deep:#5aa6c3;
  --teal:#62b0c9;
  --ink:#222;
  --text:#555;
  --muted:#888;
  --light:#f4f4f4;
  --white:#fff;
  --black:#111;
}
*{box-sizing:border-box;margin:0;padding:0}
html,body{width:1200px;height:4852px;overflow:hidden}
body{font-family:"Lato",sans-serif;color:var(--text);background:var(--white);position:relative}
.abs{position:absolute}
h2.section-title{font-family:"Alegreya Sans",sans-serif;font-weight:800;font-size:32px;color:var(--ink);text-align:center;position:absolute;left:0;width:1200px}
.title-arc{position:absolute;left:540px;width:120px;height:20px}
.btn{display:flex;align-items:center;justify-content:center;font-family:"Lato",sans-serif;font-weight:900;font-size:13px;letter-spacing:1px;text-transform:uppercase;position:absolute}
.btn-teal{background:var(--teal);color:var(--white);border-radius:3px;box-shadow:0 6px 14px rgba(0,0,0,.15)}
.btn-black{background:var(--black);color:var(--white)}
.btn-white{background:var(--white);color:var(--blue-deep);box-shadow:0 6px 14px rgba(0,0,0,.12)}

/* top bar */
.top-bar{position:absolute;top:0;left:0;width:1200px;height:40px;border-bottom:1px solid #eee;font-size:12px;color:var(--ink)}
.top-phone{left:90px;top:12px;display:flex;gap:8px;align-items:center;font-weight:700}
.top-search{left:766px;top:9px;width:227px;height:22px;border:1px solid #ddd;font-size:11px;padding:4px 8px;color:var(--ink);display:flex;justify-content:space-between}
.top-social{left:1034px;top:14px;display:flex;gap:12px}
.top-social span{width:12px;height:12px;border-radius:50%;background:var(--blue-deep)}

/* header */
.site-header{position:absolute;top:40px;left:0;width:1200px;height:120px;background:var(--white);box-shadow:0 3px 8px rgba(0,0,0,.06)}
.brand{left:90px;top:42px;display:flex;align-items:center;gap:10px;font-family:"Lato",sans-serif;font-weight:700;font-size:20px;color:var(--blue-deep)}
.brand i{width:28px;height:28px;border-radius:50%;background:var(--blue-deep);display:block}
.main-nav{left:365px;top:50px;display:flex;gap:30px;font-size:13px;font-weight:700;color:var(--ink)}
.main-nav .active{border-bottom:2px solid var(--blue-deep);padding-bottom:6px}

/* hero */
.hero{position:absolute;top:160px;left:0;width:1200px;height:465px;background:linear-gradient(120deg,#cfd9df 0%,#b7c8d2 35%,#d8b9a3 55%,#a9bccb 80%,#dfe6ea 100%)}
.hero h1{position:absolute;top:150px;left:0;width:1200px;text-align:center;font-weight:300;font-size:44px;color:var(--white)}
.hero .btn{left:492px;top:292px;width:216px;height:50px}
.hero-dot{left:581px;top:378px;width:38px;height:38px;border:2px solid rgba(255,255,255,.8);border-radius:50%}

/* practice areas */
.practice{position:absolute;top:625px;left:0;width:1200px;height:555px}
.area{position:absolute;top:225px;width:230px;text-align:center}
.area-icon{width:46px;height:46px;margin:0 auto 16px;border:2px solid var(--ink);border-radius:50%}
.area h3{font-size:14px;font-weight:900;color:var(--ink);margin-bottom:18px}
.area p{font-size:12px;line-height:1.8;color:var(--muted)}
.bubbles{left:760px;top:400px;width:320px;height:130px}

/* about band */
.about-band{position:absolute;top:1180px;left:0;width:1200px;height:470px;background:var(--blue)}
.about-band h2{position:absolute;left:97px;top:60px;font-family:"Alegreya Sans",sans-serif;font-weight:800;font-size:34px;line-height:1.15;color:var(--white)}
.about-band p{position:absolute;left:97px;top:165px;width:620px;font-size:12px;line-height:1.9;color:var(--white)}
.about-band .btn{left:97px;top:350px;width:210px;height:50px}
.about-photo{left:718px;top:-10px;width:500px;height:500px;border-radius:50%;background:var(--white);box-shadow:0 10px 30px rgba(0,0,0,.15)}
.about-photo div{position:absolute;left:14px;top:14px;width:472px;height:472px;border-radius:50%;background:radial-gradient(circle at 40% 45%,#e2c2a8,#9dbb7c 60%,#6f9a55)}

/* team */
.team{position:absolute;top:1650px;left:0;width:1200px;height:940px}
.member{position:absolute;width:260px;text-align:center}
.member-photo{width:180px;height:240px;margin:0 auto;border-radius:90px 90px 20px 20px;background:linear-gradient(180deg,#d9d9d9,#b8b8b8)}
.member h3{font-family:"Alegreya Sans",sans-serif;font-weight:800;font-size:21px;color:var(--ink);margin-top:28px}
.member span{font-size:11px;color:var(--muted)}
.member-lead{left:128px;top:0;width:150px;height:110px}

/* cases */
.cases{position:absolute;top:2590px;left:0;width:1200px;height:530px;background:var(--light)}
.case{position:absolute;top:185px;width:312px;height:275px;background:linear-gradient(160deg,#6d6557,#3b3a36 70%);box-shadow:0 10px 24px rgba(0,0,0,.25)}
.case h3{position:absolute;left:22px;top:178px;font-family:"Alegreya Sans",sans-serif;font-weight:800;font-size:23px;color:var(--white)}
.case .btn{top:222px;height:28px;font-size:10px;letter-spacing:.5px}
.case .agree{left:22px;width:120px;background:var(--teal);color:var(--white)}
.case .disagree{left:152px;width:140px;border:1px solid var(--white);color:var(--white)}
.case-dots{position:absolute;right:18px;top:16px;display:flex;gap:8px}
.case-dots i{width:8px;height:8px;border-radius:50%;background:rgba(255,255,255,.8)}

/* free book */
.free-book{position:absolute;top:3120px;left:0;width:1200px;height:550px}
.book-cover{left:194px;top:170px;width:292px;height:350px;background:linear-gradient(180deg,var(--blue-deep) 0%,var(--blue-deep) 48%,#8ea8b6 48%,#5f7d8d 100%);box-shadow:8px 14px 24px rgba(0,0,0,.25)}
.book-cover h4{position:absolute;left:18px;top:22px;font-size:22px;font-weight:700;color:var(--white)}
.book-cover p{position:absolute;left:18px;top:60px;width:240px;font-size:9px;line-height:1.6;color:var(--white)}
.book-text{left:534px;top:182px;width:400px}
.book-text h3{font-weight:400;font-size:16px;color:var(--ink)}
.book-text h5{font-weight:400;font-size:13px;color:var(--muted);margin-top:6px}
.book-text p{font-size:12px;line-height:1.8;color:var(--muted);margin-top:22px}
.free-book .btn{left:534px;top:338px;width:150px;height:48px}

/* contact */
.contact{position:absolute;top:3670px;left:0;width:1200px;height:650px;background:linear-gradient(180deg,var(--blue) 0%,#8cc1d6 60%,#5aa6c3 100%)}
.contact h2{position:absolute;left:0;top:70px;width:1200px;text-align:center;font-family:"Alegreya Sans",sans-serif;font-weight:800;font-size:32px;color:var(--white)}
.contact .lead{position:absolute;left:0;top:182px;width:1200px;text-align:center;font-size:13px;font-weight:700;color:var(--white)}
.field{position:absolute;left:194px;width:395px;height:48px;border:1px solid rgba(255,255,255,.8);font-size:11px;color:var(--white);padding:15px 14px}
.field-message{left:615px;top:340px;width:391px;height:180px}
.contact .btn{left:495px;top:561px;width:210px;height:51px}

/* footer */
.site-footer{position:absolute;top:4320px;left:0;width:1200px;height:495px;background:var(--white)}
.foot-col{position:absolute;top:73px;font-size:11px;line-height:2.05;color:var(--text)}
.foot-col h4{font-size:13px;font-weight:900;color:var(--ink);margin-bottom:14px}
.foot-col h4.sub{margin-top:20px;margin-bottom:6px}
.map{left:615px;top:112px;width:481px;height:308px;background:linear-gradient(135deg,#e8e6e1,#d6d9dc)}
.map-card{position:absolute;left:210px;top:40px;width:260px;height:150px;background:rgba(60,60,60,.85);color:var(--white);padding:20px 22px;font-size:11px;line-height:1.6}
.map-card strong{font-size:13px;display:block;margin-bottom:4px}
.map-card .btn{position:static;display:inline-flex;margin-top:10px;width:110px;height:28px;font-size:9px;background:var(--teal);color:var(--white)}
.map-pin{left:135px;top:130px;width:18px;height:26px}
.bottom-bar{position:absolute;top:4815px;left:0;width:1200px;height:37px;border-top:1px solid #eee;font-size:11px;color:var(--text);display:flex;align-items:center;justify-content:space-between;padding:0 60px 0 113px}
.bottom-bar strong{color:var(--ink);font-weight:900}
</style>
</head>
<body>

<div class="top-bar">
  <div class="abs top-phone">
    <svg width="12" height="12" viewBox="0 0 24 24"><path d="M6.6 10.8a15 15 0 0 0 6.6 6.6l2.2-2.2a1 1 0 0 1 1-.25 11.4 11.4 0 0 0 3.6.6 1 1 0 0 1 1 1V20a1 1 0 0 1-1 1A17 17 0 0 1 3 4a1 1 0 0 1 1-1h3.5a1 1 0 0 1 1 1c0 1.25.2 2.45.57 3.57a1 1 0 0 1-.25 1z" fill="#222"/></svg>
    Call: (08) 9000 4127
  </div>
  <div class="abs top-search"><span>Search</span>
    <svg width="12" height="12" viewBox="0 0 24 24"><circle cx="10" cy="10" r="6" fill="none" stroke="#5aa6c3" stroke-width="2.5"/><path d="M15 15l6 6" stroke="#5aa6c3" stroke-width="2.5"/></svg>
  </div>
  <div class="abs top-social"><span></span><span></span><span></span><span></span></div>
</div>

<header class="site-header">
  <div class="abs brand"><i></i>Kelvale Heel Care</div>
  <nav class="abs main-nav">
    <span class="active">Home</span>
    <span>Common Problems ▾</span>
    <span>Services ▾</span>
    <span>About Us ▾</span>
    <span>Case Histories</span>
    <span>Helpful Information ▾</span>
    <span>Blog</span>
    <span>Contact</span>
  </nav>
</header>

<section class="hero">
  <div class="abs" role="img" aria-label="Photo of a podiatrist's hands examining a patient's foot" style="inset:0"></div>
  <h1>We offer solutions to common foot problems</h1>
  <div class="btn btn-teal">Book Now</div>
  <div class="abs hero-dot"></div>
</section>

<section class="practice">
  <h2 class="section-title" style="top:82px">Practice Areas</h2>
  <svg class="title-arc" style="top:138px" viewBox="0 0 120 20"><path d="M2 18 Q60 -6 118 18" fill="none" stroke="#7fb9d1" stroke-width="2"/></svg>
  <div class="area" style="left:105px"><div class="area-icon"></div><h3>Common Problems</h3><p>When you suffer from a foot or ankle problem, even simple walking becomes hard and tiring, so daily activities suffer.</p></div>
  <div class="area" style="left:357px"><div class="area-icon"></div><h3>Foot &amp; Ankle Problems</h3><p>Foot and ankle pain can be very distressing and affect your daily life, and some conditions may need surgery.</p></div>
  <div class="area" style="left:610px"><div class="area-icon"></div><h3>Sports &amp; Dance</h3><p>Special patient groups have unique needs and constant strain keeps their feet and bodies healthy.</p></div>
  <div class="area" style="left:862px"><div class="area-icon"></div><h3>All Our Services</h3><p>Foot, toe or ankle pain can be treated and it can improve your ability to walk, travel, work or do the activities you enjoy.</p></div>
  <div class="btn btn-black" style="left:495px;top:462px;width:210px;height:51px">View All Areas</div>
  <svg class="abs bubbles" viewBox="0 0 320 130">
    <circle cx="270" cy="42" r="40" fill="#7fb9d1"/>
    <circle cx="195" cy="68" r="22" fill="#a9d0e0"/>
    <circle cx="140" cy="92" r="17" fill="#a9d0e0"/>
    <circle cx="92" cy="108" r="12" fill="#c7e1eb"/>
    <circle cx="52" cy="116" r="9" fill="#c7e1eb"/>
    <circle cx="20" cy="120" r="6" fill="#dbecf2"/>
  </svg>
</section>

<section class="about-band">
  <h2>Let Our Kelvale Podiatrists<br>Relieve Your Foot and Ankle Pain</h2>
  <p>Whether you are an older patient, an active sports person, a keen runner or simply have sore heels after a long day, our podiatrists are here to help you. We treat a wide range of common foot and ankle conditions, from heel pain and bunions to ingrown toenails, flat feet and sports injuries. Our caring team takes time to listen, explains every option clearly and works with you on a plan that suits your lifestyle. We also offer surgical care for more complex problems, so you can get back on your feet sooner and keep doing the things you love.</p>
  <div class="btn btn-white">Read More</div>
  <div class="abs about-photo"><div role="img" aria-label="Photo of hands holding a bare foot on green grass"></div></div>
</section>

<section class="team">
  <h2 class="section-title" style="top:68px">Meet Our Team</h2>
  <svg class="title-arc" style="top:124px" viewBox="0 0 120 20"><path d="M2 18 Q60 -6 118 18" fill="none" stroke="#7fb9d1" stroke-width="2"/></svg>
  <div class="member" style="left:129px;top:178px"><div class="member-photo" role="img" aria-label="Portrait of podiatric surgeon Ruth Callan"></div></div>
  <svg class="abs member-lead" style="top:400px" viewBox="0 0 150 110">
    <rect x="24" y="8" width="120" height="62" rx="31" fill="#7fb9d1"/>
    <circle cx="16" cy="66" r="11" fill="#7fb9d1"/>
    <circle cx="10" cy="90" r="7" fill="#7fb9d1"/>
    <text x="84" y="36" text-anchor="middle" font-family="Alegreya Sans, sans-serif" font-weight="800" font-size="17" fill="#fff">Ruth Callan</text>
    <text x="84" y="54" text-anchor="middle" font-family="Lato, sans-serif" font-size="9" fill="#fff">Podiatric Surgeon</text>
  </svg>
  <div class="member" style="left:468px;top:178px"><div class="member-photo" role="img" aria-label="Portrait of podiatrist Owen Brackley"></div><h3>Owen Brackley</h3><span>Podiatrist</span></div>
  <div class="member" style="left:811px;top:178px"><div class="member-photo" role="img" aria-label="Portrait of podiatrist Priya Dunmore"></div><h3>Priya Dunmore</h3><span>Podiatrist</span></div>
  <div class="member" style="left:129px;top:533px"><div class="member-photo" role="img" aria-label="Portrait of podiatrist Nell Hartigan"></div><h3>Nell Hartigan</h3><span>Podiatrist</span></div>
  <div class="member" style="left:468px;top:533px"><div class="member-photo" role="img" aria-label="Portrait of podiatrist Jess Orwin"></div><h3>Jess Orwin</h3><span>Podiatrist</span></div>
  <div class="member" style="left:811px;top:533px"><div class="member-photo" role="img" aria-label="Portrait of podiatrist Clare Sowden"></div><h3>Clare Sowden</h3><span>Podiatrist</span></div>
</section>

<section class="cases">
  <h2 class="section-title" style="top:72px">Case Histories</h2>
  <svg class="title-arc" style="top:128px" viewBox="0 0 120 20"><path d="M2 18 Q60 -6 118 18" fill="none" stroke="#7fb9d1" stroke-width="2"/></svg>
  <div class="case" style="left:110px" role="img" aria-label="Photo of a runner holding a sore heel">
    <div class="case-dots"><i></i><i></i><i></i></div>
    <h3>Plantar fascia Case</h3><div class="btn agree">I Agree</div><div class="btn disagree">I Don't Agree</div>
  </div>
  <div class="case" style="left:446px;background:linear-gradient(160deg,#8a8a8a,#3d3d3d 70%)" role="img" aria-label="Photo of a foot with a bunion">
    <div class="case-dots"><i></i><i></i><i></i></div>
    <h3>Bunion Case</h3><div class="btn agree">I Agree</div><div class="btn disagree">I Don't Agree</div>
  </div>
  <div class="case" style="left:780px;background:linear-gradient(160deg,#6f8a5c,#33402c 70%)" role="img" aria-label="Photo of running shoes on a path">
    <div class="case-dots"><i></i><i></i><i></i></div>
    <h3>Trauma case</h3><div class="btn agree">I Agree</div><div class="btn disagree">I Don't Agree</div>
  </div>
</section>

<section class="free-book">
  <h2 class="section-title" style="top:58px">Free Book</h2>
  <svg class="title-arc" style="top:114px" viewBox="0 0 120 20"><path d="M2 18 Q60 -6 118 18" fill="none" stroke="#7fb9d1" stroke-width="2"/></svg>
  <div class="abs book-cover" role="img" aria-label="Book cover showing surgeons in an operating theatre">
    <h4>Podiatric Surgery</h4>
    <p>Dr Ruth Callan, Podiatric Surgeon<br>A guide to common foot conditions and their care</p>
  </div>
  <div class="abs book-text">
    <h3>Dr Ruth Callan</h3>
    <h5>Free Foot Surgery Book by Podiatric Surgeon</h5>
    <p>This book was created to show clear examples of foot conditions that can be surgically corrected by our Podiatric Surgeon, Dr Ruth Callan.</p>
  </div>
  <div class="btn btn-teal">Book Now</div>
</section>

<section class="contact">
  <h2>Contact Us</h2>
  <div class="lead">Please fill out this quick contact form and someone will be in touch with you shortly!</div>
  <div class="field" style="top:340px">Name*</div>
  <div class="field" style="top:412px">E-Mail*</div>
  <div class="field" style="top:484px">Phone*</div>
  <div class="field field-message">Tell Us More</div>
  <div class="btn btn-black">Submit</div>
</section>

<footer class="site-footer">
  <div class="foot-col" style="left:113px">
    <h4>Common Services</h4>
    Achilles Tendon Injuries<br>Ankle Sprains<br>Bunions<br>Corns and callouses<br>Heel and Arch Pain<br>High Arch Feet (Pes Cavus)<br>Ingrown Toenails<br>Fungal Nails<br>Flatfeet<br>Morton's Neuroma<br>Skin and Nail Care<br>Stiff Big Toe (Hallux Rigidus)
  </div>
  <div class="foot-col" style="left:401px">
    <h4>Services</h4>
    Foot &amp; Ankle Surgery<br>Sport and Dance<br>All Our Services
    <h4 class="sub">About Us</h4>
    About Us<br>Ruth Callan<br>Owen Brackley<br>Priya Dunmore<br>Nell Hartigan<br>Jess Orwin<br>Clare Sowden
  </div>
  <div class="foot-col" style="left:615px"><h4>Get Directions</h4></div>
  <div class="abs map" role="img" aria-label="Street map showing the Kelvale clinic location">
    <svg class="abs map-pin" viewBox="0 0 18 26"><path d="M9 0a9 9 0 0 1 9 9c0 7-9 17-9 17S0 16 0 9a9 9 0 0 1 9-9z" fill="#d9463b"/><circle cx="9" cy="9" r="3.5" fill="#fff"/></svg>
    <div class="map-card">
      <strong>Kelvale Office</strong>
      14 Wattle Road | Kelvale WA 6999<br>Phone: (08) 9000 4127
      <div class="btn">Get Directions</div>
    </div>
  </div>
</footer>

<div class="bottom-bar">
  <span><strong>Helpful Information</strong> » Articles &nbsp;| &nbsp;FAQs &nbsp;| &nbsp;Educational Videos &nbsp;| &nbsp;Free Offers &nbsp;| &nbsp;Newsletter</span>
  <span>© 2017 Company Name &nbsp;| &nbsp;All Rights Reserved</span>
</div>

</body>
</html>
```